Need help in designing new business card utilizing our new logo.

BuildMark Solutions works with Construction Business Owners, Managers & IT Professionals to strengthen software usage and increase user productivity.

Our Construction Accounting and Mobile Field Management Software Clients engage with us in the following areas:

New Software Implementations
Software Re-Implementations
Redesigning Software Usage at the User Level
Project Coordination & Management
Continued Software Support

Old tag line:
Clear Choices - Working Systems

www.buildmark-solutions.example

Ridge 4 is a product, but not needed for a new business card.

```html
<!DOCTYPE html>
<html lang="en">
<head>
<meta charset="utf-8">
<title>BuildMark Solutions Business Card</title>
<link href="https://fonts.googleapis.com/css2?family=Roboto:wght@400;500;700&display=swap" rel="stylesheet">
<style>
  :root {
    --backdrop: #3a3b3e;
    --card: #24262a;
    --brand-blue: #0b3f8c;
    --accent-blue: #1d5fc4;
    --text-light: #f2f3f5;
    --text-muted: #c9ccd1;
    --mark-grey: #8d9096;
    --mark-dark: #15161a;
  }
  * { box-sizing: border-box; margin: 0; padding: 0; }
  html, body {
    width: 799px; height: 1200px; overflow: hidden;
    background: var(--backdrop);
    font-family: "Roboto", Arial, sans-serif;
  }
  .canvas {
    position: relative; width: 799px; height: 1200px;
    display: flex; flex-direction: column; align-items: center;
    justify-content: center; gap: 140px;
  }
  .card {
    position: relative; width: 630px; height: 360px;
    background: var(--card); border-radius: 22px; overflow: hidden;
    box-shadow: 0 14px 30px rgba(0,0,0,.35);
  }
  .brand {
    display: flex; align-items: center; gap: 14px;
    font-weight: 500; text-transform: uppercase; letter-spacing: 2px;
  }
  .brand-square { width: 38px; height: 38px; flex: none; }
  .brand-name { font-size: 30px; line-height: 1; }

  /* Front */
  .card-front .brand { position: absolute; top: 58px; left: 0; right: 0; justify-content: center; }
  .card-front .brand-square { background: var(--mark-dark); }
  .card-front .brand-name { color: var(--mark-grey); }
  .services {
    position: absolute; top: 162px; left: 0; right: 0; height: 120px;
    background: var(--brand-blue); color: var(--text-light);
    display: flex; flex-direction: column; justify-content: center;
    align-items: center; gap: 4px; font-size: 17px; line-height: 1.25;
  }
  .front-web {
    position: absolute; top: 302px; left: 0; right: 0;
    display: flex; justify-content: center; align-items: center; gap: 18px;
    color: var(--text-light); font-size: 16px;
  }
  .front-web .rule { width: 40px; height: 2px; background: var(--text-muted); }

  /* Back */
  .card-back .brand { position: absolute; top: 70px; left: 40px; }
  .card-back .brand-square { background: var(--accent-blue); }
  .card-back .brand-name { color: var(--accent-blue); font-size: 26px; }
  .contact { position: absolute; top: 72px; left: 310px; right: 24px; color: var(--text-light); }
  .person-name { color: var(--accent-blue); font-weight: 700; font-size: 22px; }
  .person-role { color: var(--text-muted); font-size: 13px; margin: 2px 0 14px; }
  .address { font-size: 14px; line-height: 1.35; margin-bottom: 12px; }
  .lines { list-style: none; font-size: 13.5px; line-height: 1.55; }
  .lines li { display: flex; align-items: center; gap: 9px; white-space: nowrap; }
  .lines svg { width: 12px; height: 12px; fill: var(--accent-blue); flex: none; }
  .tagline-band {
    position: absolute; left: 0; right: 0; bottom: 0; height: 52px;
    background: var(--brand-blue); color: var(--text-light);
    display: flex; align-items: center; padding-left: 48px; font-size: 16px;
  }
</style>
</head>
<body>
<main class="canvas">
  <section class="card card-front" aria-label="Card front">
    <div class="brand">
      <span class="brand-square"></span>
      <span class="brand-name">BuildMark Solutions</span>
    </div>
    <div class="services">
      <p>New Software Implementations &nbsp;|&nbsp; Software Re-Implementations</p>
      <p>Redesigning Software Usage at the User Level</p>
      <p>Project Coordination &amp; Management &nbsp;|&nbsp; Continued Software Support</p>
    </div>
    <div class="front-web">
      <span class="rule"></span>
      <span>www.buildmark-solutions.example</span>
      <span class="rule"></span>
    </div>
  </section>

  <section class="card card-back" aria-label="Card back">
    <div class="brand">
      <span class="brand-square"></span>
      <span class="brand-name">BuildMark<br>Solutions</span>
    </div>
    <div class="contact">
      <p class="person-name">Dana R. Whitley</p>
      <p class="person-role">Owner</p>
      <p class="address">14B Harbor Lane - Suite 118<br>Millbrook, NY 12545</p>
      <ul class="lines">
        <li><svg viewBox="0 0 12 12"><path d="M2 1h2.5l1 3-1.5 1a6 6 0 0 0 3 3l1-1.5 3 1V10a1 1 0 0 1-1 1A9 9 0 0 1 1 2a1 1 0 0 1 1-1z"/></svg>555-201-4836</li>
        <li><svg viewBox="0 0 12 12"><path d="M2 1h2.5l1 3-1.5 1a6 6 0 0 0 3 3l1-1.5 3 1V10a1 1 0 0 1-1 1A9 9 0 0 1 1 2a1 1 0 0 1 1-1z"/></svg>555-208-7731 ext. 100</li>
        <li><svg viewBox="0 0 12 12"><path d="M1 2.5h10v7H1zM1.5 3l4.5 3.5L10.5 3" stroke="#24262a" stroke-width="1"/></svg>dana.whitley@buildmark-solutions.example</li>
        <li><svg viewBox="0 0 12 12"><circle cx="6" cy="6" r="5"/><path d="M1 6h10M6 1c-2 3-2 7 0 10M6 1c2 3 2 7 0 10" stroke="#24262a" stroke-width=".8" fill="none"/></svg>www.buildmark-solutions.example</li>
      </ul>
    </div>
    <div class="tagline-band">Clear Choices - Working Systems</div>
  </section>
</main>
</body>
</html>
```